Upmarket Dessert Lounge needs a Business Card Design

We are an upmarket dessert lounge needing a business card to match our image.

We want something that is simple yet beautiful, feminine, classy, sophisticated and elegant. We want it to stand out and don't mind if it is bold.

The design should include our logo and colours of red or maroon with gold highlights. We don't mind if black is used.

Marlow & Quince

Target Market(s)

For those who like to indulge or treat themselves and give in to their temptations on good quality desserts.

Industry/Entity Type

Business

Requirements
Must have
• Must include our logo and our name

Marlow & Quince

M & Q

```html
<!DOCTYPE html>
<html lang="en">
<head>
<meta charset="utf-8">
<title>Marlow &amp; Quince – Business Card</title>
<link rel="stylesheet" href="https://fonts.googleapis.com/css2?family=Source+Sans+3:wght@400;600;700&display=swap">
<style>
  :root {
    --backdrop: #d9d9d9;
    --card-black: #000000;
    --cream: #ffd49b;
    --logo-cream: #f6d9a2;
    --maroon: #7c1416;
    --ink-maroon: #6e1214;
  }
  * { box-sizing: border-box; margin: 0; padding: 0; }
  html, body {
    width: 956px; height: 1200px; overflow: hidden;
    background: var(--backdrop);
    font-family: "Source Sans 3", "Myriad Pro", Arial, sans-serif;
  }
  .card {
    position: absolute;
    width: 797px; height: 455px;
    border-radius: 28px;
    background: var(--card-black);
    overflow: hidden;
  }
  .card--front { left: 80px; top: 117px; }
  .card--back { left: 75px; top: 634px; }

  .card__wave { position: absolute; inset: 0; width: 797px; height: 455px; }

  .brand-name {
    position: absolute;
    transform: translate(-50%, -50%);
    color: var(--logo-cream);
    font-weight: 600;
    white-space: nowrap;
    letter-spacing: 1px;
  }
  .card--front .brand-name { left: 191px; top: 190px; font-size: 78px; }
  .card--back .brand-name { left: 397px; top: 228px; font-size: 112px; }

  .address {
    position: absolute;
    left: 183px; top: 368px;
    transform: translateX(-50%);
    text-align: center;
    color: var(--cream);
    font-size: 19px;
    line-height: 27px;
    white-space: nowrap;
  }

  .contact {
    position: absolute;
    left: 607px;
    transform: translateX(-50%);
    text-align: center;
    color: var(--ink-maroon);
    white-space: nowrap;
  }
  .contact__name { top: 84px; font-size: 25px; font-weight: 700; line-height: 30px; }
  .contact__role { top: 114px; font-size: 19px; line-height: 24px; }
  .contact__lines { top: 220px; font-size: 19px; line-height: 36px; }
  .contact__web { top: 367px; font-size: 19px; line-height: 33px; }
  .contact .label { font-weight: 700; }
</style>
</head>
<body>
  <section class="card card--front" aria-label="Business card front">
    <svg class="card__wave" viewBox="0 0 797 455" aria-hidden="true">
      <path fill="var(--maroon)" d="M392,90 C392,210 445,300 432,360 C425,400 400,430 380,455 L400,455 C450,370 448,290 405,205 C385,165 385,120 392,90 Z"/>
      <path fill="var(--cream)" d="M412,0 C375,55 378,150 405,205 C448,290 452,365 402,455 L797,455 L797,0 Z"/>
    </svg>

    <div class="brand-name">M &amp; Q</div>

    <p class="address">0000, Street Name<br>City Name, Country Code.</p>

    <p class="contact contact__name">Your Name</p>
    <p class="contact contact__role">Designation</p>
    <p class="contact contact__lines">
      <span class="label">p</span> : 123-456-7890<br>
      <span class="label">c</span> : 123-456-7890<br>
      <span class="label">f</span> : 123-456-7890
    </p>
    <p class="contact contact__web">
      <span class="label">e</span> : name@yourwebsite.com<br>
      <span class="label">w</span> : www.marlow&amp;quince.com
    </p>
  </section>

  <section class="card card--back" aria-label="Business card back">
    <div class="brand-name">M &amp; Q</div>
  </section>
</body>
</html>
```